High-end construction company needs a business card design

We need a modern looking business card that draws people in, is memorable and looks so good people will want to sick it on their fridges.
On the first side what is needed are:
Logo
My name - Tomasz Brelwik
Title - Managing Director
Website - www.varkelt.co.uk
Email - tomasz@varkelt.co.uk
Telephone - 020 5194 6281
Mobile - 07845139072
On the back side was is needed is a list of all the services we provide:
-Kitchen Renovations
-Bathroom Renovations
-House Renovations
-Garage Conversions
-Extensions
-Loft Conversions
-Conservatories
-Carpentry
-Tiling
-Electrical
-Plumbing & Heating
-Bricklaying
-Landscaping
-Decorating
-Plastering
We would like the colours to be the same shades as on the logo with grey or black for the words.
Target Market(s)
Anyone who needs building work done
Contact Information for Business Card
This business card is for a construction company which strives to deliver excellent service and quality.
The look and feel of the card should represent this.
Requirements
Must have
- On the first side what is needed are:
Logo
My name - Tomasz Brelwik
Title - Managing Director
Website - www.varkelt.co.uk
Email - tomasz@varkelt.co.uk
Telephone - 020 5194 6281
Mobile - 07845139072
Nice to have
- Cool looking features

```html
<!DOCTYPE html>
<html lang="en">
<head>
<meta charset="utf-8">
<title>Varkelt Construction Ltd – Business Card</title>
<link href="https://fonts.googleapis.com/css2?family=Exo+2:wght@300;400;600;700&display=swap" rel="stylesheet">
<style>
  :root {
    --backdrop: #e6e6e6;
    --card-white: #ffffff;
    --green-light: #7cc35a;
    --green-mid: #5ea548;
    --green-deep: #3f8a3c;
    --green-back-dark: #2f7630;
    --green-back-light: #6aa563;
    --text-grey: #555a55;
    --text-white: #f4f8f3;
  }
  * { box-sizing: border-box; margin: 0; padding: 0; }
  html, body {
    width: 1200px; height: 1200px; overflow: hidden;
    background: var(--backdrop);
    font-family: "Exo 2", sans-serif;
  }
  .card {
    position: absolute; left: 262px;
    width: 686px; height: 391px;
    overflow: hidden;
  }
  .card--front { top: 165px; background: var(--card-white); }
  .card--back {
    top: 653px;
    background: linear-gradient(30deg, var(--green-back-dark) 0%, var(--green-mid) 60%, var(--green-back-light) 100%);
  }

  .hero-art {
    position: absolute; left: 0; top: 20px;
    width: 418px; height: 371px;
    background: linear-gradient(150deg, var(--green-light) 0%, var(--green-mid) 55%, var(--green-deep) 100%);
    border-top-right-radius: 170px 140px;
  }

  .brand {
    position: absolute; left: 444px; top: 62px; width: 200px;
    color: var(--green-light); font-weight: 700; text-align: center;
  }
  .brand__mark {
    width: 34px; height: 34px; border-radius: 50%;
    background: var(--green-light); margin: 0 auto 8px;
  }
  .brand__name { font-size: 16px; letter-spacing: 1.5px; line-height: 1.25; text-transform: uppercase; }

  .person {
    position: absolute; right: 43px; top: 196px; text-align: right;
  }
  .person__name {
    font-size: 22px; font-weight: 700; letter-spacing: 0.8px;
    color: var(--green-mid); text-transform: uppercase; line-height: 1.1;
    white-space: nowrap;
  }
  .person__title {
    font-size: 13px; font-weight: 600; color: var(--green-deep);
    text-transform: uppercase; margin-top: 2px;
  }

  .contacts {
    position: absolute; right: 46px; top: 262px; list-style: none;
    color: var(--text-grey); font-size: 15.5px; font-weight: 400;
  }
  .contacts li {
    display: flex; align-items: center; justify-content: flex-end;
    gap: 8px; height: 20.6px; white-space: nowrap;
  }
  .contacts svg { width: 12px; height: 12px; fill: var(--green-mid); }

  .services {
    position: absolute; top: 112px; list-style: none;
    color: var(--text-white); font-size: 15px; font-weight: 300; letter-spacing: 0.3px;
  }
  .services--left { left: 135px; }
  .services--right { left: 383px; top: 111px; }
  .services li { display: flex; align-items: center; gap: 9px; height: 21.4px; }
  .services svg { width: 12px; height: 12px; flex: none; }
</style>
</head>
<body>

<section class="card card--front">
  <div class="hero-art" role="img" aria-label="Green illustration of an excavator arm and bucket over tall buildings and a house roof"></div>

  <div class="brand">
    <div class="brand__mark"></div>
    <div class="brand__name">Varkelt<br>Construction Ltd</div>
  </div>

  <div class="person">
    <div class="person__name">Tomasz Brelwik</div>
    <div class="person__title">Managing Director</div>
  </div>

  <ul class="contacts">
    <li>020 5194 6281
      <svg viewBox="0 0 24 24"><path d="M6.6 10.8a15 15 0 0 0 6.6 6.6l2.2-2.2c.3-.3.7-.4 1-.2 1.1.4 2.3.6 3.6.6.6 0 1 .4 1 1V20c0 .6-.4 1-1 1A17 17 0 0 1 3 4c0-.6.4-1 1-1h3.5c.6 0 1 .4 1 1 0 1.3.2 2.5.6 3.6.1.3 0 .7-.2 1z"/></svg></li>
    <li>07845139072
      <svg viewBox="0 0 24 24"><path d="M7 1h10a2 2 0 0 1 2 2v18a2 2 0 0 1-2 2H7a2 2 0 0 1-2-2V3a2 2 0 0 1 2-2zm0 3v14h10V4zm4 15.5v1.5h2v-1.5z"/></svg></li>
    <li>tomasz@varkelt.co.uk
      <svg viewBox="0 0 24 24"><path d="M2 5h20v14H2zm2 2v.5l8 5 8-5V7zm0 3v7h16v-7l-8 5z"/></svg></li>
    <li>www.varkelt.co.uk
      <svg viewBox="0 0 24 24"><path d="M12 2a10 10 0 1 0 0 20 10 10 0 0 0 0-20zm-1 17.9A8 8 0 0 1 4.2 10L9 15v1a2 2 0 0 0 2 2zm6.9-2.5A2 2 0 0 0 16 16h-1v-3a1 1 0 0 0-1-1H8v-2h2a1 1 0 0 0 1-1V7h2a2 2 0 0 0 2-2v-.4a8 8 0 0 1 2.9 12.8z"/></svg></li>
  </ul>
</section>

<section class="card card--back">
  <ul class="services services--left">
    <li><svg viewBox="0 0 12 12"><rect x="0.75" y="0.75" width="10.5" height="10.5" fill="none" stroke="#fff" stroke-width="1.5"/><path d="M3 6.2l2 2 4-4.4" fill="none" stroke="#fff" stroke-width="1.7"/></svg>Kitchen Renovations</li>
    <li><svg viewBox="0 0 12 12"><rect x="0.75" y="0.75" width="10.5" height="10.5" fill="none" stroke="#fff" stroke-width="1.5"/><path d="M3 6.2l2 2 4-4.4" fill="none" stroke="#fff" stroke-width="1.7"/></svg>Bathroom Renovations</li>
    <li><svg viewBox="0 0 12 12"><rect x="0.75" y="0.75" width="10.5" height="10.5" fill="none" stroke="#fff" stroke-width="1.5"/><path d="M3 6.2l2 2 4-4.4" fill="none" stroke="#fff" stroke-width="1.7"/></svg>House Renovations</li>
    <li><svg viewBox="0 0 12 12"><rect x="0.75" y="0.75" width="10.5" height="10.5" fill="none" stroke="#fff" stroke-width="1.5"/><path d="M3 6.2l2 2 4-4.4" fill="none" stroke="#fff" stroke-width="1.7"/></svg>Garage Conversions</li>
    <li><svg viewBox="0 0 12 12"><rect x="0.75" y="0.75" width="10.5" height="10.5" fill="none" stroke="#fff" stroke-width="1.5"/><path d="M3 6.2l2 2 4-4.4" fill="none" stroke="#fff" stroke-width="1.7"/></svg>Extensions</li>
    <li><svg viewBox="0 0 12 12"><rect x="0.75" y="0.75" width="10.5" height="10.5" fill="none" stroke="#fff" stroke-width="1.5"/><path d="M3 6.2l2 2 4-4.4" fill="none" stroke="#fff" stroke-width="1.7"/></svg>Loft Conversions</li>
    <li><svg viewBox="0 0 12 12"><rect x="0.75" y="0.75" width="10.5" height="10.5" fill="none" stroke="#fff" stroke-width="1.5"/><path d="M3 6.2l2 2 4-4.4" fill="none" stroke="#fff" stroke-width="1.7"/></svg>Conservatories</li>
    <li><svg viewBox="0 0 12 12"><rect x="0.75" y="0.75" width="10.5" height="10.5" fill="none" stroke="#fff" stroke-width="1.5"/><path d="M3 6.2l2 2 4-4.4" fill="none" stroke="#fff" stroke-width="1.7"/></svg>Carpentry</li>
  </ul>
  <ul class="services services--right">
    <li><svg viewBox="0 0 12 12"><rect x="0.75" y="0.75" width="10.5" height="10.5" fill="none" stroke="#fff" stroke-width="1.5"/><path d="M3 6.2l2 2 4-4.4" fill="none" stroke="#fff" stroke-width="1.7"/></svg>Tiling</li>
    <li><svg viewBox="0 0 12 12"><rect x="0.75" y="0.75" width="10.5" height="10.5" fill="none" stroke="#fff" stroke-width="1.5"/><path d="M3 6.2l2 2 4-4.4" fill="none" stroke="#fff" stroke-width="1.7"/></svg>Electrical</li>
    <li><svg viewBox="0 0 12 12"><rect x="0.75" y="0.75" width="10.5" height="10.5" fill="none" stroke="#fff" stroke-width="1.5"/><path d="M3 6.2l2 2 4-4.4" fill="none" stroke="#fff" stroke-width="1.7"/></svg>Plumbing &amp; Heating</li>
    <li><svg viewBox="0 0 12 12"><rect x="0.75" y="0.75" width="10.5" height="10.5" fill="none" stroke="#fff" stroke-width="1.5"/><path d="M3 6.2l2 2 4-4.4" fill="none" stroke="#fff" stroke-width="1.7"/></svg>Bricklaying</li>
    <li><svg viewBox="0 0 12 12"><rect x="0.75" y="0.75" width="10.5" height="10.5" fill="none" stroke="#fff" stroke-width="1.5"/><path d="M3 6.2l2 2 4-4.4" fill="none" stroke="#fff" stroke-width="1.7"/></svg>Landscaping</li>
    <li><svg viewBox="0 0 12 12"><rect x="0.75" y="0.75" width="10.5" height="10.5" fill="none" stroke="#fff" stroke-width="1.5"/><path d="M3 6.2l2 2 4-4.4" fill="none" stroke="#fff" stroke-width="1.7"/></svg>Decorating</li>
    <li><svg viewBox="0 0 12 12"><rect x="0.75" y="0.75" width="10.5" height="10.5" fill="none" stroke="#fff" stroke-width="1.5"/><path d="M3 6.2l2 2 4-4.4" fill="none" stroke="#fff" stroke-width="1.7"/></svg>Plastering</li>
  </ul>
</section>

</body>
</html>
```